HOT TUB - SPAS service needs an business card

I need an business for my company who his specialise in a maintenance,water treatment and cleaning of Hot Tub - Spas for commercial and residential customers. The company operate mainly in the ski resort of Chamonix, Megève and St Gervais. The final product should communicate pure water, cleanest and professional for luxury property's.
I have upload a logo but any improvement on it is welcome.(color,size, details etc..) or any other idea. Thank you
Company Name: 58 BAINS
My name: Lucien Marchetti
Email: lucimarch@examplemail.net
Tel: +33 (0)6 71 58 29 64
Description to be on the card in french(first langage) and in English:
- Spas service
- Entretien, traitement eau, nettoyage.
- Maintenance, water treatment, cleaning.
Industry/Entity Type
Residential
Colors
Designer to choose colors to be used in the design.
Look and feel
Each slider illustrates characteristics of the customer's brand and the style your logo design should communicate.

```html
<!DOCTYPE html>
<html lang="fr">
<head>
<meta charset="utf-8">
<title>58 BAINS – Carte de visite</title>
<link rel="stylesheet" href="https://fonts.googleapis.com/css2?family=Open+Sans:wght@400;600;700&display=swap">
<style>
  :root {
    --stage: #eef1f4;
    --water-light: #3aa6f2;
    --water-mid: #2292ea;
    --water-deep: #1a7fd6;
    --ink: #ffffff;
    --ink-soft: rgba(255,255,255,0.92);
    --card-shadow: rgba(20,40,70,0.22);
  }
  * { margin: 0; padding: 0; box-sizing: border-box; }
  html, body {
    width: 1200px; height: 1087px; overflow: hidden;
    background: var(--stage);
    font-family: "Open Sans", Arial, sans-serif;
    color: var(--ink);
  }
  .sheet { position: relative; width: 1200px; height: 1087px; }
  .card {
    position: absolute; width: 859px; height: 489px; overflow: hidden;
    box-shadow: 0 4px 14px var(--card-shadow);
  }
  .card--front { left: 43px; top: 34px; }
  .card--back  { left: 279px; top: 544px; }
  .card__texture {
    position: absolute; inset: 0;
    background:
      radial-gradient(ellipse at 30% 20%, var(--water-light) 0%, transparent 60%),
      radial-gradient(ellipse at 80% 85%, var(--water-deep) 0%, transparent 65%),
      var(--water-mid);
  }
  .brand-name {
    position: absolute; font-weight: 600; font-size: 49px; line-height: 1;
    letter-spacing: 0.5px; white-space: nowrap;
  }
  .card--front .brand-name { left: 239px; top: 186px; }
  .card--back .brand-name { left: 0; right: 0; top: 150px; text-align: center; }
  .contact {
    position: absolute; right: 18px; top: 232px; text-align: right;
  }
  .contact__name { font-weight: 700; font-size: 27px; line-height: 1; margin-bottom: 24px; }
  .contact__line {
    display: flex; justify-content: flex-end; align-items: center; gap: 10px;
    font-size: 26px; line-height: 1; margin-bottom: 26px; color: var(--ink-soft);
  }
  .contact__icon { width: 22px; height: 22px; flex: none; }
  .services {
    position: absolute; left: 0; right: 0; top: 340px; text-align: center;
  }
  .services__title { font-weight: 600; font-size: 27px; line-height: 1; margin-bottom: 14px; }
  .services__list { font-size: 28px; line-height: 40px; color: var(--ink-soft); }
  .services__list span::before { content: "• "; }
  .services__list span + span { margin-left: 10px; }
</style>
</head>
<body>
<main class="sheet">

  <section class="card card--front" aria-label="Recto">
    <div class="card__texture" role="img" aria-label="Gouttes d'eau sur fond bleu"></div>
    <div class="brand-name">58 BAINS</div>
    <div class="contact">
      <p class="contact__name">Lucien Marchetti</p>
      <p class="contact__line">
        <svg class="contact__icon" viewBox="0 0 24 24" aria-hidden="true">
          <circle cx="12" cy="12" r="10.5" fill="none" stroke="#fff" stroke-width="1.6"/>
          <path d="M8.5 6.5c-1.2 1.5-.9 4.3 1.6 7.2 2.4 2.8 5 3.7 6.6 2.6l-1.8-2.3-1.6.8c-1-.6-2.3-2.1-2.8-3.2l1.1-1.4z" fill="#fff"/>
        </svg>
        +33 (0)6 71 58 29 64
      </p>
      <p class="contact__line">
        <svg class="contact__icon" viewBox="0 0 24 24" aria-hidden="true">
          <rect x="2" y="7" width="20" height="13" rx="1.5" fill="#fff"/>
          <path d="M2.5 8l9.5 6.5L21.5 8" fill="none" stroke="#2292ea" stroke-width="1.6"/>
          <path d="M5 7l7-4 7 4" fill="none" stroke="#fff" stroke-width="1.6"/>
        </svg>
        lucimarch@examplemail.net
      </p>
    </div>
  </section>

  <section class="card card--back" aria-label="Verso">
    <div class="card__texture" role="img" aria-label="Gouttes d'eau sur fond bleu"></div>
    <div class="brand-name">58 BAINS</div>
    <div class="services">
      <p class="services__title">SPAS SERVICES</p>
      <p class="services__list"><span>Entretien</span><span>traitement eau</span><span>nettoyage</span></p>
      <p class="services__list"><span>Maintenance</span><span>water treatment</span><span>cleaning.</span></p>
    </div>
  </section>

</main>
</body>
</html>
```